mobile app - telecom industry

We are a tech/service company. Our product is a mobile application for physical site inspection called “Vorn”. Our target industry is telecommunica...

Target Market(s)

telecommunication

Industry/Entity Type

Industry

Requirements
Must have
• Screen size Quorin 5 - Android
• Suggest 3 colors
• Design 9 pages

```html
<!DOCTYPE html>
<html lang="en">
<head>
<meta charset="utf-8">
<title>Vorn – Landing Page</title>
<link rel="stylesheet" href="https://fonts.googleapis.com/css2?family=Open+Sans:wght@300;400&display=swap">
<style>
  :root {
    --backdrop: #e4e4e4;
    --teal: #47b2a8;
    --rule: #86d0c8;
    --white: #ffffff;
  }
  * { box-sizing: border-box; margin: 0; padding: 0; }
  html, body {
    width: 1200px;
    height: 1200px;
    overflow: hidden;
    background: var(--backdrop);
    font-family: "Open Sans", sans-serif;
  }
  .screen {
    position: absolute;
    left: 284px;
    top: 40px;
    width: 632px;
    height: 1120px;
    background: var(--teal);
    color: var(--white);
    font-weight: 300;
  }
  .status-bar {
    position: absolute;
    top: 4px;
    left: 8px;
    right: 8px;
    height: 22px;
    font-size: 17px;
    font-weight: 400;
    display: flex;
    align-items: center;
  }
  .status-bar .carrier { display: flex; align-items: center; gap: 8px; }
  .status-bar .signal { letter-spacing: -2px; font-size: 13px; }
  .status-bar .wifi { margin-left: 20px; }
  .status-bar .clock { position: absolute; left: 50%; transform: translateX(-50%); }
  .status-bar .battery { margin-left: auto; display: flex; align-items: center; gap: 10px; }
  .status-bar .battery-cell {
    width: 40px; height: 11px; background: var(--white); position: relative;
  }
  .status-bar .battery-cell::after {
    content: ""; position: absolute; right: -4px; top: 3px; width: 3px; height: 5px; background: var(--white);
  }
  .brand-mark {
    position: absolute;
    left: 194px;
    top: 105px;
    width: 242px;
    height: 242px;
    border-radius: 50%;
    background: var(--white);
  }
  .brand-name {
    position: absolute;
    top: 372px;
    width: 100%;
    text-align: center;
    font-size: 76px;
    font-weight: 300;
    line-height: 1;
  }
  .field {
    position: absolute;
    left: 41px;
    width: 548px;
    border-bottom: 2px solid var(--rule);
    font-size: 30px;
    line-height: 1.2;
    padding-bottom: 4px;
  }
  .field-login { top: 647px; }
  .field-password { top: 747px; }
  .btn {
    position: absolute;
    top: 826px;
    height: 67px;
    border: 2px solid var(--rule);
    border-radius: 5px;
    font-size: 30px;
    font-weight: 300;
    display: flex;
    align-items: center;
    justify-content: center;
  }
  .btn-forgot { left: 40px; width: 293px; }
  .btn-go { left: 432px; width: 157px; }
  .btn-signup {
    position: absolute;
    left: 169px;
    top: 975px;
    width: 292px;
    height: 67px;
    border-radius: 8px;
    background: var(--white);
  }
</style>
</head>
<body>
  <main class="screen">
    <div class="status-bar">
      <span class="carrier"><span class="signal">●●●●●</span> Telvo</span>
      <svg class="wifi" width="24" height="17" viewBox="0 0 24 17" aria-hidden="true">
        <path d="M12 16 L8 12 A6 6 0 0 1 16 12 Z" fill="#fff"/>
        <path d="M5 9 A10 10 0 0 1 19 9" stroke="#fff" stroke-width="2.5" fill="none"/>
        <path d="M1.5 5.5 A15 15 0 0 1 22.5 5.5" stroke="#fff" stroke-width="2.5" fill="none"/>
      </svg>
      <span class="clock">11:59</span>
      <span class="battery">100% <span class="battery-cell"></span></span>
    </div>

    <div class="brand-mark" aria-hidden="true"></div>
    <h1 class="brand-name">Vorn</h1>

    <div class="field field-login">Login or Email</div>
    <div class="field field-password">Password</div>

    <div class="btn btn-forgot">Forgot Password</div>
    <div class="btn btn-go">GO!</div>

    <div class="btn-signup"></div>
  </main>
</body>
</html>
```